BrivoTerna. Lantern of the Steady Harvest. Business card

Professional business card for BrivoTerna (Lantern of the Steady Harvest)
My rationale: Strategy-> Execution-> Results-> Value that lead to the BrivoTerna name: We put the Lantern of the Steady Harvest.
We deliver value to our customers helping them at defining a good strategy (cyan arrow). 90% of well formulated strategies fail due to poor execution so we also consider strategical execution very important (green arrow). Due to the execution we obtain the results (blue arrow). Finally, the results provide feedback to redefine strategy, and the new strategy has to be executed and new results obtained providing new feedback and on and on. It's like a wheel that finally, must create corporate value: value for shareholders, staholders, employees, providers...-

Target Market(s)

CEOs and steering comitees , invewrnent funds

Industry/Entity Type

Business Consultant

Contact Information for Business Card

Teodoro Vinsquel
CEO & Founder
teodoro.vinsquel@brivoterna-example.com
Mobile: +34 655.803.912
www.brivoterna-example.com

Colors

Designer to choose colors to be used in the design.

Requirements
Nice to have
• Nice to hace the words: Strategy, execution, results
• Nice to vave the claim: Lantern of the Steady Harvest
• The three colors should be shown:
• cyan for STRATEGY
• green for EXECUTION
• blue for RESULTS
Should not have
• Complete black background

```html
<!DOCTYPE html>
<html lang="en">
<head>
<meta charset="utf-8">
<title>BrivoTerna – Business Card</title>
<link rel="stylesheet" href="https://fonts.googleapis.com/css2?family=Open+Sans:wght@400;600;700&display=swap">
<style>
  :root {
    --navy: #0d3592;
    --cyan: #1ea9e6;
    --green: #8cc63f;
    --ink: #3a3a3a;
    --paper: #ffffff;
    --backdrop: #e7e4e1;
    --divider: #d9d9d9;
  }
  * { box-sizing: border-box; margin: 0; padding: 0; }
  html, body {
    width: 1200px;
    height: 997px;
    overflow: hidden;
    background: var(--backdrop);
    font-family: "Open Sans", Arial, sans-serif;
  }
  .stage {
    position: relative;
    width: 1200px;
    height: 997px;
  }
  .card {
    position: absolute;
    left: 320px;
    width: 560px;
    height: 320px;
    background: var(--paper);
    box-shadow: 0 10px 24px rgba(0,0,0,0.12);
  }
  .card--contact { top: 150px; }
  .card--brand { top: 530px; }

  /* contact side */
  .contact-brand {
    position: absolute;
    left: 0;
    top: 0;
    width: 240px;
    height: 320px;
    display: flex;
    align-items: center;
    justify-content: center;
    gap: 10px;
  }
  .brand-dot {
    width: 16px;
    height: 16px;
    border-radius: 50%;
    background: var(--navy);
  }
  .brand-name {
    color: var(--navy);
    font-weight: 700;
    font-size: 32px;
    letter-spacing: -0.5px;
  }
  .contact-divider {
    position: absolute;
    left: 248px;
    top: 40px;
    width: 1px;
    height: 120px;
    background: var(--divider);
  }
  .contact-details {
    position: absolute;
    left: 268px;
    top: 42px;
    color: var(--ink);
  }
  .person-name {
    color: var(--navy);
    font-weight: 700;
    font-size: 19px;
    line-height: 1.1;
  }
  .person-role {
    font-size: 13px;
    margin-top: 2px;
    margin-bottom: 14px;
  }
  .contact-line {
    display: flex;
    align-items: center;
    gap: 8px;
    font-size: 12px;
    line-height: 19px;
  }
  .contact-line svg { width: 11px; height: 11px; flex: none; }
  .pillars {
    position: absolute;
    right: 0;
    bottom: 70px;
    width: 300px;
    height: 80px;
  }
  .pillar-label {
    fill: #fff;
    font-family: "Open Sans", Arial, sans-serif;
    font-size: 14px;
    font-weight: 400;
  }

  /* brand side */
  .brand-block {
    position: absolute;
    inset: 0;
    display: flex;
    flex-direction: column;
    align-items: center;
    justify-content: center;
  }
  .brand-block .brand-row {
    display: flex;
    align-items: center;
    gap: 14px;
  }
  .brand-block .brand-dot { width: 22px; height: 22px; }
  .brand-block .brand-name { font-size: 52px; }
  .tagline {
    display: flex;
    align-items: center;
    gap: 10px;
    margin-top: 10px;
    color: var(--navy);
    font-size: 13px;
  }
  .tagline-rule {
    width: 70px;
    height: 1px;
    background: var(--cyan);
  }
</style>
</head>
<body>
<main class="stage">

  <section class="card card--contact" aria-label="Business card, contact side">
    <div class="contact-brand">
      <span class="brand-dot"></span>
      <span class="brand-name">BrivoTerna</span>
    </div>
    <div class="contact-divider"></div>
    <div class="contact-details">
      <p class="person-name">Teodoro Vinsquel</p>
      <p class="person-role">CEO &amp; Founder</p>
      <p class="contact-line">
        <svg viewBox="0 0 12 12" aria-hidden="true"><rect x="3" y="0.5" width="6" height="11" rx="1" fill="none" stroke="#0d3592" stroke-width="1.2"/><circle cx="6" cy="9.6" r="0.7" fill="#0d3592"/></svg>
        +34 655.803.912
      </p>
      <p class="contact-line">
        <svg viewBox="0 0 12 12" aria-hidden="true"><rect x="0.5" y="2.5" width="11" height="7" fill="#0d3592"/><path d="M0.5 2.5 L6 6.5 L11.5 2.5" fill="none" stroke="#fff" stroke-width="1"/></svg>
        teodoro.vinsquel@brivoterna-example.com
      </p>
      <p class="contact-line">
        <svg viewBox="0 0 12 12" aria-hidden="true"><circle cx="6" cy="6" r="5.3" fill="#0d3592"/><path d="M0.8 6 H11.2 M6 0.8 C3.5 3.5 3.5 8.5 6 11.2 M6 0.8 C8.5 3.5 8.5 8.5 6 11.2" fill="none" stroke="#fff" stroke-width="0.8"/></svg>
        www.brivoterna-example.com
      </p>
    </div>
    <svg class="pillars" viewBox="0 0 300 80" aria-hidden="true">
      <polygon points="10,54 104,54 96,80 0,80" fill="var(--cyan)"/>
      <text class="pillar-label" x="52" y="72" text-anchor="middle">Strategy</text>
      <polygon points="108,28 202,28 194,54 100,54" fill="var(--green)"/>
      <text class="pillar-label" x="150" y="46" text-anchor="middle">Execution</text>
      <polygon points="206,0 300,0 300,28 198,28" fill="var(--navy)"/>
      <text class="pillar-label" x="250" y="19" text-anchor="middle">Results</text>
    </svg>
  </section>

  <section class="card card--brand" aria-label="Business card, brand side">
    <div class="brand-block">
      <div class="brand-row">
        <span class="brand-dot"></span>
        <span class="brand-name">BrivoTerna</span>
      </div>
      <p class="tagline">
        <span class="tagline-rule"></span>
        Lantern of the Steady Harvest
        <span class="tagline-rule"></span>
      </p>
    </div>
  </section>

</main>
</body>
</html>
```